Stylish new business card needed!

Hello everyone! I am in need of a new business card design for an alarm company here in Hurricane WV. I have all fonts, color codes and logos provided for you use! We are a young company and like the style of a clean sleek looking business card. Would like it double sided, one side holding the logo and the other with your design!
Target Market(s)
The people that are looking for the newest tech for home automation and security
Industry/Entity Type
Alarm services; Home automation
Contact Information for Business Card
Name of person; position (Sales; Installer); Phone Number (555.418.7260); Employee cell Number; Website (www.GuardedByVelk.example); Employee Email; Double sided
Look and feel
Each slider illustrates characteristics of the customer's brand and the style your logo design should communicate.

```html
<!DOCTYPE html>
<html lang="en">
<head>
<meta charset="utf-8">
<title>Velk Business Card</title>
<link href="https://fonts.googleapis.com/css2?family=Arimo:wght@400;700&display=swap" rel="stylesheet">
<style>
  :root {
    --orange: #ec8a4b;
    --grey: #9a9a9a;
    --ink: #1a1a1a;
    --paper: #f5f5f5;
    --backdrop: #2b2f36;
  }
  * { margin: 0; padding: 0; box-sizing: border-box; }
  html, body { width: 1200px; height: 780px; overflow: hidden; }
  body {
    background: var(--backdrop);
    font-family: "Arimo", Arial, sans-serif;
    position: relative;
  }
  .card {
    position: absolute;
    top: 230px;
    width: 560px;
    height: 320px;
    overflow: hidden;
  }
  .card--front { left: 30px; background: var(--paper); }
  .card--back { left: 610px; background: var(--orange); }

  .front-swoosh { position: absolute; inset: 0; }

  .brand { position: absolute; left: 300px; top: 48px; }
  .brand-name {
    display: flex; align-items: center; gap: 12px;
    font-size: 72px; font-weight: 700; color: var(--grey);
    letter-spacing: 2px; line-height: 1;
  }
  .brand-dot {
    width: 22px; height: 22px; border-radius: 50%;
    background: var(--orange);
  }
  .brand-tagline {
    margin-top: 8px;
    font-size: 8px; font-weight: 700; color: var(--orange);
    letter-spacing: 0.6px;
  }

  .person { position: absolute; left: 110px; top: 100px; }
  .person-name { font-size: 26px; font-weight: 700; line-height: 1; }
  .person-first { color: var(--orange); }
  .person-last { color: var(--grey); }
  .person-role {
    margin-top: 8px; margin-left: 40px;
    font-size: 14px; font-weight: 700; color: var(--ink);
  }

  .divider {
    position: absolute; left: 232px; top: 170px;
    width: 2px; height: 92px; background: var(--ink);
  }

  .contacts {
    position: absolute; left: 250px; top: 172px;
    list-style: none;
  }
  .contact {
    display: flex; align-items: center; gap: 8px;
    font-size: 17px; color: var(--ink); line-height: 22px;
  }
  .contact svg { width: 12px; height: 12px; flex: none; }

  .back-field {
    position: absolute; inset: 0;
    background: linear-gradient(135deg, #ee9156 0%, var(--orange) 55%, #e07f41 100%);
  }
  .back-brand {
    position: absolute; right: 60px; bottom: 52px;
    color: #ffffff;
  }
  .back-brand .brand-name { font-size: 30px; color: #ffffff; gap: 6px; }
  .back-brand .brand-dot { width: 10px; height: 10px; background: #ffffff; }
  .back-brand .brand-tagline { color: #ffffff; font-size: 5px; margin-top: 4px; }
</style>
</head>
<body>

<section class="card card--front" aria-label="Card front">
  <svg class="front-swoosh" viewBox="0 0 560 320" width="560" height="320" aria-hidden="true">
    <path d="M0,85 C40,225 220,300 560,302 L560,320 L0,320 Z" fill="var(--orange)"/>
    <path d="M28,62 C70,205 230,286 520,290" fill="none" stroke="var(--grey)" stroke-width="5" stroke-linecap="round"/>
  </svg>

  <div class="brand">
    <div class="brand-name">VELK<span class="brand-dot"></span></div>
    <div class="brand-tagline">AUTOMATION AND SECURITY SERVICES</div>
  </div>

  <div class="person">
    <div class="person-name"><span class="person-first">Dana</span> <span class="person-last">Whitfield</span></div>
    <div class="person-role">Sales; Installer</div>
  </div>

  <div class="divider"></div>

  <ul class="contacts">
    <li class="contact">
      <svg viewBox="0 0 12 12" aria-hidden="true"><path d="M2.5 1 L4.5 1 L5 3.5 L3.8 4.4 C4.5 6 6 7.5 7.6 8.2 L8.5 7 L11 7.5 L11 9.5 C11 10.3 10.3 11 9.5 11 C5 11 1 7 1 2.5 C1 1.7 1.7 1 2.5 1 Z" fill="var(--orange)"/></svg>
      555.418.7260
    </li>
    <li class="contact">
      <svg viewBox="0 0 12 12" aria-hidden="true"><rect x="3" y="1" width="6" height="10" rx="1" fill="none" stroke="var(--orange)" stroke-width="1.2"/></svg>
      555.418.3391
    </li>
    <li class="contact">
      <svg viewBox="0 0 12 12" aria-hidden="true"><circle cx="6" cy="6" r="5" fill="var(--orange)"/><path d="M1 6 H11 M6 1 C3.5 3.5 3.5 8.5 6 11 M6 1 C8.5 3.5 8.5 8.5 6 11" fill="none" stroke="#fff" stroke-width="0.8"/></svg>
      www.GuardedByVelk.example
    </li>
    <li class="contact">
      <svg viewBox="0 0 12 12" aria-hidden="true"><rect x="1" y="2.5" width="10" height="7" fill="var(--orange)"/><path d="M1 2.5 L6 6.5 L11 2.5" fill="none" stroke="#fff" stroke-width="0.9"/></svg>
      info@GuardedByVelk.example
    </li>
  </ul>
</section>

<section class="card card--back" aria-label="Card back">
  <div class="back-field" role="img" aria-label="Repeating brand wordmark pattern on orange"></div>
  <div class="back-brand">
    <div class="brand-name">VELK<span class="brand-dot"></span></div>
    <div class="brand-tagline">AUTOMATION AND SECURITY SERVICES</div>
  </div>
</section>

</body>
</html>
```